Oak Flooring Brochure (need asap!)

advertising our range of Oak flooring products using exciting photos taken of recent jobs we have completed.
We will use these jobs to showcase our high end LUXURY product aimed at the architectural market.
Main page will feature the current property we are promoting (214b harrowby lane mckinnon) see below:
http://www.homefindr.com.au/property-townhouse-vic-mckinnon-528374610

Please use the following photos for the main front of the brochure:

http://files07.listingvault.com.au/images/512847390615283947106283741952/Original27381946.jpg

smaller:
http://files07.listingvault.com.au/images/512847390615283947106283741952/Original27385021.jpg
same size as above?:

http://files07.listingvault.com.au/images/512847390615283947106283741952/Original27385369.jpg

please use my logo that you have from my past project.
my contact number:
0417286940
email:
brenlyx@postmiro.com

back side use the following pics:

past projects:
52 Dorrit Avenue

http://files07.listingvault.com.au/images/274019583620174839205718364027/Original28461037.jpg
http://files07.listingvault.com.au/images/274019583620174839205718364027/Original28460192.jpg
And the ones I sent you via email.

*I would like this in a double sided a4*

Text from page:
one version with open for inspection times and auction date (see homefindr.com.au link) the other without.

front:

business name. My contact details: Reno Bellavista Director.

Why us:
We work closely with local estate agents and have intimate knowledge of buyer requirements thus maximising sale price
We offer the most competitive prices

Back:

We specialize in wide engineered timber floors with board widths of 158mm, 189mm, 260mm and can go up to as wide as 410mm.
We create special finishes and colors tailored for the Australian market
We use thick top layers on well-constructed Oak bases to ensure stability and long life unlike others who use multiply.
20mm – multiply construction.
6mm Oak Layer with 14mm base.(use pic as sent to you buy divide the last two layers so that the bottom is 4mm and middle is 1 cm.

benefits of Engineered flooring:
Far greater stability means less floor failures than with solid floors.
Available in a range of pre-finished, hard to achieve colors
Reduced installation time due to pre-finished product.
Can be secret-nailed or just glued down, unlike solid boards which, if over 90mm wide, require top-nailing..
Updates

Please note, I require a design sooner rather than later.  thanks!

Please see recent changes to must have's, please use logo's Ive just updated.

Brochure needs to clearly look like we are advertising the Oak flooring.  Invitation/flyer so this must entice people to come and inspect or call for more information.

Consider adding:

Call to action.
"30% off until Christmas!"

"affordable quick way to modernise, update the look and feel of your home!"

FINAL DESIGNS CLOSING IN 24 HOURS, PLEASE SUBMIT FINAL CHANGES.  THANKS

Target Market(s)

architects, developers, mums and dads looking to renovate their homes.

Industry/Entity Type

Advertising

Font styles to use
Other font styles liked:
• GeometricSlab

Requirements
Must have
• our logo, information above
clear uncluttered info
Nice to have
• A similar banner over the main photo on front page of brochure similar to:
http://www.plankerly.com.au

with the saying

The Architects Choice
Elegant, Leading Edge & Affordable.

use these words below, mix them up, creative jigsaw......

Should not have
• too many colors (white is gold)

```html
<!DOCTYPE html>
<html lang="en">
<head>
<meta charset="utf-8">
<title>Engineered Oak Flooring</title>
<link rel="stylesheet" href="https://fonts.googleapis.com/css2?family=Arimo:wght@400;700&display=swap">
<style>
  :root {
    --crimson: #8c0a2b;
    --crimson-soft: rgba(140, 10, 43, 0.86);
    --ink: #2b2b2b;
    --paper: #ffffff;
    --frame-shadow: #d9d9d9;
    --wood-light: #d8c6ad;
    --wood-mid: #b49a7a;
    --wood-pale: #e9dfd0;
  }
  * { margin: 0; padding: 0; box-sizing: border-box; }
  html, body { width: 927px; height: 1200px; overflow: hidden; background: var(--paper); }
  body { font-family: "Arimo", Arial, sans-serif; color: var(--ink); }
  .page { position: relative; width: 927px; height: 1200px; overflow: hidden; background: var(--paper); }

  .photo { position: absolute; border-radius: 3px; }
  .photo--boards { left: 39px; top: 42px; width: 276px; height: 181px;
    background: linear-gradient(100deg, var(--wood-pale), var(--wood-light) 45%, var(--wood-mid)); }
  .photo--interior { left: 330px; top: 42px; width: 275px; height: 181px;
    background: linear-gradient(180deg, #7d7f7a 0%, #a7a39a 40%, #b29b7d 70%, #8c7358 100%); }
  .photo--rug { left: 618px; top: 42px; width: 277px; height: 181px;
    background: linear-gradient(160deg, #c9b8a3, #b8a48c 55%, #e8e2da); }

  .copy { position: absolute; font-size: 22px; letter-spacing: 0.3px; white-space: nowrap; }
  .intro { left: 44px; top: 236px; line-height: 27px; }

  .frame-shadow { position: absolute; left: 52px; top: 331px; width: 257px; height: 197px; background: var(--frame-shadow); }
  .photo--hallway { left: 44px; top: 323px; width: 253px; height: 185px; border-radius: 0; border: 2px solid var(--paper);
    background: linear-gradient(180deg, #e6e4df 0%, #c8c2b5 45%, #b2906a 75%, #9a7853 100%); }

  .finishes-lead { left: 331px; top: 309px; line-height: 28px; }
  .finishes-accent { left: 331px; top: 338px; line-height: 40px; color: var(--crimson); font-size: 27px; letter-spacing: 0.2px; }
  .finishes-accent strong { font-weight: 400; font-size: 38px; }
  .finishes-body { left: 332px; top: 382px; line-height: 27px; }
  .finishes-spec { left: 332px; top: 469px; line-height: 33px; }

  .benefits-title { position: absolute; left: 42px; top: 546px; color: var(--crimson); font-size: 31.5px; font-weight: 700; line-height: 36px; white-space: nowrap; }
  .benefits-list { position: absolute; left: 42px; top: 591px; list-style: none; font-size: 22px; letter-spacing: 0.3px; white-space: nowrap; }
  .benefits-item { position: relative; padding-left: 42px; line-height: 30.5px; }
  .benefits-tick { position: absolute; left: 0; top: 6px; width: 27px; height: 22px; }

  .lower-scene { position: absolute; left: 0; top: 720px; width: 927px; height: 480px; }

  .cta-banner { position: absolute; left: 332px; top: 973px; width: 595px; height: 104px; background: var(--crimson-soft);
    color: var(--paper); padding: 15px 0 0 24px; font-size: 30.5px; line-height: 31px; white-space: nowrap; }

  .contact-line { position: absolute; left: 48px; top: 1156px; color: var(--paper); font-size: 21px; line-height: 24px; font-weight: 700;
    white-space: nowrap; text-shadow: 0 1px 2px rgba(0,0,0,0.25); }
</style>
</head>
<body>
<main class="page">
  <div class="photo photo--boards" role="img" aria-label="Close-up of wide pale oak floorboards"></div>
  <div class="photo photo--interior" role="img" aria-label="Open living room with oak floor and glass doors to a courtyard"></div>
  <div class="photo photo--rug" role="img" aria-label="Limed oak floor with a zebra-print hide rug"></div>

  <p class="copy intro">We specialize in wide engineered timber floors with board widths of 158mm,<br>189mm, 260mm and can go up to as wide as 410mm.</p>

  <div class="frame-shadow"></div>
  <div class="photo photo--hallway" role="img" aria-label="Long hallway with oak floor and window seat cushions"></div>

  <p class="copy finishes-lead">We create special finishes and</p>
  <p class="copy finishes-accent">colors tailored for the <strong>Australian market</strong></p>
  <p class="copy finishes-body">We use thick top layers on well-constructed Oak<br>bases to ensure stability and long life unlike others<br>who use multiply.</p>
  <p class="copy finishes-spec">20mm – multiply construction.<br>6mm Oak Layer with 14mm base</p>

  <svg class="lower-scene" viewBox="0 0 927 480" aria-hidden="true">
    <defs>
      <linearGradient id="room-tone" x1="0" y1="0" x2="0" y2="1">
        <stop offset="0" stop-color="#f2efe9"/>
        <stop offset="0.4" stop-color="#ebe6dd"/>
        <stop offset="0.65" stop-color="#d8c6ad"/>
        <stop offset="1" stop-color="#c9a672"/>
      </linearGradient>
    </defs>
    <path d="M0 86 Q464 179 927 68 V480 H0 Z" fill="url(#room-tone)"/>
    <path d="M0 8 Q464 144 927 12 V68 Q464 179 0 86 Z" fill="#8c0a2b"/>
  </svg>
  <div class="lower-scene" style="pointer-events:none" role="img" aria-label="Bright modern lounge with white sofa on a light oak floor"></div>

  <h2 class="benefits-title">Benefits of Engineered flooring:</h2>
  <ul class="benefits-list">
    <li class="benefits-item"><svg class="benefits-tick" viewBox="0 0 27 22"><path d="M1 12 L6 9 L11 15 L24 1 L26 4 L11 21 Z" fill="#8c0a2b"/></svg>Far greater stability means less floor failures than with solid floors.</li>
    <li class="benefits-item"><svg class="benefits-tick" viewBox="0 0 27 22"><path d="M1 12 L6 9 L11 15 L24 1 L26 4 L11 21 Z" fill="#8c0a2b"/></svg>Available in a range of pre-finished, hard to achieve colors</li>
    <li class="benefits-item"><svg class="benefits-tick" viewBox="0 0 27 22"><path d="M1 12 L6 9 L11 15 L24 1 L26 4 L11 21 Z" fill="#8c0a2b"/></svg>Reduced installation time due to pre-finished product.</li>
    <li class="benefits-item"><svg class="benefits-tick" viewBox="0 0 27 22"><path d="M1 12 L6 9 L11 15 L24 1 L26 4 L11 21 Z" fill="#8c0a2b"/></svg>Can be secret-nailed or just glued down, unlike solid boards which, if over 90mm<br>wide, require top-nailing..</li>
  </ul>

  <div class="cta-banner">Affordable quick way to modernise,<br>update the look and feel of your home!</div>

  <p class="contact-line">Call us Now 0417286940&nbsp; or&nbsp; email:brenlyx@postmiro.com</p>
</main>
</body>
</html>
```